Financial Services Company power point theme design

We need a PowerPoint theme designed for client presentations and company orientations. We do like modern designs using blue colors. attached is our logos the logo colors may change as needed to fit the theme. Landscape 16: 9 is acceptable

Industry/Entity Type

Financial Service

Colors

Designer to choose colors to be used in the design.

```html
<!DOCTYPE html>
<html lang="en">
<head>
<meta charset="utf-8">
<title>Keystone Harbor Finance – Presentation Theme</title>
<link href="https://fonts.googleapis.com/css2?family=Merriweather:wght@700;900&family=Open+Sans:wght@400;600;700&display=swap" rel="stylesheet">
<style>
:root{
  --navy:#1e3a6e;
  --navy-deep:#15295099;
  --navy-dark:#142a55;
  --navy-soft:#2c4c86;
  --grey:#7b7f86;
  --grey-light:#c9ccd2;
  --ink:#3a3d44;
  --paper:#ffffff;
  --board:#eef0f3;
  --photo-a:#b9c3d1;
  --photo-b:#8e9cb2;
}
*{box-sizing:border-box;margin:0;padding:0}
html,body{width:993px;height:1200px;overflow:hidden;background:var(--board)}
body{font-family:"Open Sans",Arial,sans-serif;color:var(--ink)}
.board{
  display:grid;grid-template-columns:repeat(3,298px);grid-template-rows:repeat(5,223px);
  gap:10px 14px;padding:22px 0 0 35px;
}
.slide{position:relative;overflow:hidden;background:var(--paper);box-shadow:0 1px 3px rgba(0,0,0,.18)}
.slide.dark{background:var(--navy)}
.abs{position:absolute}
.shapes{position:absolute;inset:0;width:100%;height:100%}
.photo{position:absolute;background:linear-gradient(135deg,var(--photo-a),var(--photo-b))}

/* brand */
.brand{position:absolute;top:9px;right:12px;display:flex;align-items:center;gap:4px;
  font:700 5.6px/1.15 "Merriweather",Georgia,serif;color:var(--navy);text-transform:uppercase;letter-spacing:.2px}
.brand i{display:block;width:9px;height:9px;background:var(--navy)}
.brand.light{color:#fff}.brand.light i{background:#fff}

/* headings */
.hd{position:absolute;left:14px;font:700 10.5px/1 "Merriweather",Georgia,serif;color:var(--navy);text-transform:uppercase;letter-spacing:.2px}
.hd::before{content:"";position:absolute;left:-14px;top:1px;border-left:6px solid var(--navy);border-top:4.5px solid transparent;border-bottom:4.5px solid transparent}
.hd.light{color:#fff}.hd.light::before{border-left-color:#fff}
.title{position:absolute;font:700 14.5px/1.1 "Merriweather",Georgia,serif;color:var(--navy)}
.subtitle{position:absolute;font:700 7.5px/1.1 "Merriweather",Georgia,serif;color:var(--navy)}
.light{color:#fff}
.sub{position:absolute;font:700 6px/1.2 "Open Sans",Arial,sans-serif;color:var(--navy);text-transform:uppercase}
.body{position:absolute;font:400 5.4px/1.45 "Open Sans",Arial,sans-serif;color:var(--ink)}
.body.b{font-weight:700;color:#222}
.body.w{color:#e6ebf3}
.small{position:absolute;font:400 4.4px/1.4 "Open Sans",Arial,sans-serif;color:var(--ink)}
.small.w{color:#dfe5ef}
.lbl{position:absolute;font:700 5.4px/1.2 "Open Sans",Arial,sans-serif;color:var(--navy)}

/* footer */
.foot{position:absolute;left:0;right:0;bottom:0;height:14px}
.foot .bar{position:absolute;left:0;right:0;bottom:0;height:4px;background:var(--navy)}
.foot .url{position:absolute;left:10px;bottom:6px;font:600 3.8px/1 "Open Sans",Arial,sans-serif;color:var(--navy);text-transform:uppercase}
.foot .pg{position:absolute;right:0;bottom:0;width:26px;height:12px;background:var(--paper);
  clip-path:polygon(9px 0,100% 0,100% 100%,0 100%);font:700 5.5px/12px "Open Sans",Arial,sans-serif;color:var(--navy);text-align:right;padding-right:5px}
.foot .pg::before{content:"";position:absolute;left:3px;bottom:0;border-bottom:7px solid var(--navy);border-right:6px solid transparent}
.dark .foot .bar{background:var(--navy-dark)}
.dark .foot .url{color:#fff}

/* list */
.bullets{position:absolute;list-style:none;font:400 5.4px/1.9 "Open Sans",Arial,sans-serif;color:var(--ink)}
.bullets li::before{content:"";display:inline-block;width:3.5px;height:3.5px;background:var(--navy);margin-right:4px;vertical-align:middle}

.step{position:absolute;width:28px;height:28px;border-radius:50%;border:2px solid #fff;color:#fff;
  font:700 8px/24px "Open Sans",Arial,sans-serif;text-align:center}
.member{position:absolute;width:36px;height:36px;background:linear-gradient(135deg,#d7dbe1,#9aa2ad);border:1.5px solid var(--grey-light)}
.name{position:absolute;font:700 6.5px/1 "Open Sans",Arial,sans-serif;color:var(--navy)}
.contact{position:absolute;left:40px;top:160px;list-style:none;font:400 5.4px/1 "Open Sans",Arial,sans-serif;color:var(--ink)}
.contact li{display:flex;align-items:center;gap:5px;margin-bottom:5px}
.contact svg{width:8px;height:8px}
</style>
</head>
<body>
<main class="board">

<!-- 1 title light -->
<section class="slide">
  <div class="brand"><i></i><span>Keystone Harbor<br>Finance LLC.</span></div>
  <div class="title" style="left:62px;top:94px">PRESENTATION TITLE</div>
  <div class="subtitle" style="left:62px;top:112px">Presentation Subtitle Goes Here</div>
  <svg class="shapes" viewBox="0 0 237 178" preserveAspectRatio="none">
    <defs><linearGradient id="ph1" x1="0" y1="0" x2="1" y2="1"><stop offset="0" stop-color="#d9dde3"/><stop offset="1" stop-color="#b7a898"/></linearGradient></defs>
    <polygon points="0,96 46,122 0,150" fill="var(--navy)"/>
    <polygon points="22,160 66,134 110,160 66,186" fill="var(--navy)"/>
    <polygon points="168,128 205,106 242,128 205,150" fill="var(--navy)"/>
    <polygon points="165,98 190,84 215,98 190,112" fill="var(--navy)"/>
    <polygon points="112,162 152,138 205,168 195,178 128,178" fill="url(#ph1)" role="img" aria-label="Photo of a smiling family outdoors"/>
  </svg>
</section>

<!-- 2 title dark -->
<section class="slide dark">
  <svg class="shapes" viewBox="0 0 237 178" preserveAspectRatio="none">
    <polygon points="0,138 42,114 84,138 42,162" fill="#254680"/>
    <polygon points="60,178 102,154 144,178" fill="#254680"/>
    <polygon points="100,120 135,100 170,120 135,140" fill="#22417a"/>
  </svg>
  <div class="photo" role="img" aria-label="Photo of a businesswoman on the phone holding a tablet" style="left:182px;top:30px;width:116px;height:193px;background:linear-gradient(90deg,var(--navy),#8f9db3 35%,#c7ccd4)"></div>
  <div class="brand light" style="left:14px;right:auto;top:42px;font-size:7px"><i style="width:12px;height:12px"></i><span>Keystone Harbor<br>Finance LLC.</span></div>
  <div class="title light" style="left:12px;top:120px">PRESENTATION TITLE</div>
  <div class="subtitle light" style="left:12px;top:137px">Presentation Subtitle Goes Here</div>
</section>

<!-- 3 title light alt -->
<section class="slide">
  <div class="brand"><i></i><span>Keystone Harbor<br>Finance LLC.</span></div>
  <div class="title" style="left:60px;top:94px">PRESENTATION TITLE</div>
  <div class="subtitle" style="left:60px;top:112px">Presentation Subtitle Goes Here</div>
  <svg class="shapes" viewBox="0 0 237 178" preserveAspectRatio="none">
    <polygon points="0,92 45,118 0,144" fill="var(--navy)"/>
    <polygon points="20,178 75,146 130,178" fill="var(--navy)"/>
    <polygon points="92,124 138,98 184,124 138,150" fill="var(--navy)"/>
    <polygon points="170,154 212,130 237,144 237,178 195,178" fill="var(--navy)"/>
    <polygon points="237,94 206,112 237,130" fill="var(--navy)"/>
  </svg>
</section>

<!-- 4 welcome -->
<section class="slide">
  <div class="hd" style="top:52px">Welcome Message</div>
  <p class="body" style="left:12px;top:74px;width:142px">Lorem ipsum dolor sit amet, consectetur adipiscing elit, sed do eiusmod tempor incididunt ut labore et dolore magna aliqua. Ut enim ad minim veniam, quis nostrud exercitation ullamco laboris nisi ut aliquip ex ea commodo consequat.</p>
  <p class="body" style="left:12px;top:128px;width:142px">Duis aute irure dolor in reprehenderit in voluptate velit esse cillum dolore eu fugiat nulla pariatur reprehenderit.</p>
  <div class="photo" role="img" aria-label="Photo of a businesswoman shaking hands" style="left:165px;top:0;width:133px;height:209px;background:linear-gradient(160deg,#6f6257,#b99f86 45%,#3f3a37)"></div>
  <div class="brand light" style="top:8px;right:8px"><i></i><span>Keystone Harbor<br>Finance LLC.</span></div>
  <div class="foot"><div class="bar"></div><div class="url">www.keystoneharbor.com</div><div class="pg">13</div></div>
</section>

<!-- 5 heading -->
<section class="slide">
  <div class="brand"><i></i><span>Keystone Harbor<br>Finance LLC.</span></div>
  <div class="hd" style="top:27px">Heading Goes Here</div>
  <div class="sub" style="left:22px;top:62px">Subheading Goes Here</div>
  <p class="body" style="left:22px;top:74px;width:258px">Lorem ipsum dolor sit amet, consectetur adipiscing elit, sed do eiusmod tempor incididunt ut labore et dolore magna aliqua. Ut enim ad minim veniam, quis nostrud exercitation ullamco laboris nisi ut aliquip ex ea commodo consequat. Duis aute irure dolor in reprehenderit in voluptate velit esse cillum dolore eu fugiat nulla pariatur.</p>
  <p class="body" style="left:22px;top:120px;width:258px">Lorem ipsum dolor sit amet, consectetur adipiscing elit, sed do eiusmod tempor incididunt ut labore et dolore magna aliqua. Ut enim ad minim veniam, quis nostrud exercitation ullamco laboris nisi ut aliquip ex ea commodo consequat. Duis aute irure dolor in reprehenderit in voluptate velit esse cillum dolore eu fugiat nulla pariatur.</p>
  <div class="foot"><div class="bar"></div><div class="url">www.keystoneharbor.com</div><div class="pg">13</div></div>
</section>

<!-- 6 corner -->
<section class="slide">
  <div class="photo" role="img" aria-label="Photo of hands signing paperwork at a desk" style="left:0;top:0;width:298px;height:100px;background:linear-gradient(120deg,#8d9bb0,#c4c7cb 50%,#7d8da6)"></div>
  <div class="brand light" style="top:8px;right:8px"><i></i><span>Keystone Harbor<br>Finance LLC.</span></div>
  <div class="abs" style="left:18px;top:24px;font:700 9.5px/1 'Merriweather',Georgia,serif;color:#fff;opacity:.9">ALWAYS IN YOUR CORNER</div>
  <div class="abs" style="left:18px;top:36px;font:400 4.4px/1 'Open Sans',Arial,sans-serif;color:#fff;opacity:.8">FOR YOUR FAMILY OR YOUR BUSINESS</div>
  <div class="abs" style="left:0;right:0;top:99px;height:1px;background:var(--grey-light)"></div>
  <div class="step" style="left:46px;top:85px;background:var(--navy-dark)">1</div>
  <div class="step" style="left:134px;top:85px;background:var(--navy-soft)">2</div>
  <div class="step" style="left:222px;top:85px;background:var(--grey)">3</div>
  <div class="lbl" style="left:44px;top:125px;font-size:4.6px">TEXT GOES HERE</div>
  <div class="lbl" style="left:132px;top:125px;font-size:4.6px">TEXT GOES HERE</div>
  <div class="lbl" style="left:220px;top:125px;font-size:4.6px">TEXT GOES HERE</div>
  <p class="small" style="left:44px;top:133px;width:58px">Lorem ipsum dolor sit amet, consectetur adipiscing elit, sed do eiusmod.</p>
  <p class="small" style="left:132px;top:133px;width:58px">Lorem ipsum dolor sit amet, consectetur adipiscing elit, sed do eiusmod.</p>
  <p class="small" style="left:220px;top:133px;width:58px">Lorem ipsum dolor sit amet, consectetur adipiscing elit, sed do eiusmod.</p>
  <div class="foot"><div class="bar"></div><div class="url">www.keystoneharbor.com</div><div class="pg">13</div></div>
</section>

<!-- 7 text picture bullets -->
<section class="slide">
  <div class="brand"><i></i><span>Keystone Harbor<br>Finance LLC.</span></div>
  <div class="hd" style="top:22px">Text, Picture and Bullets</div>
  <p class="body b" style="left:12px;top:40px;width:274px;font-size:5px">Lorem ipsum dolor sit amet, consectetur adipiscing elit, sed do eiusmod tempor incididunt ut labore et dolore magna aliqua. <span style="font-weight:400">Ut enim ad minim veniam, quis nostrud exercitation ullamco laboris nisi ut aliquip ex ea commodo consequat velit esse cillum dolore eu fugiat nulla pariatur.</span></p>
  <div class="abs" style="left:42px;top:112px;width:8px;height:66px;background:var(--navy)"></div>
  <div class="abs" style="left:42px;top:170px;width:60px;height:8px;background:var(--navy)"></div>
  <div class="photo" role="img" aria-label="Photo of a family together at home" style="left:54px;top:120px;width:50px;height:46px"></div>
  <ul class="bullets" style="left:186px;top:102px">
    <li>Lorem ipsum dolor sit amet</li><li>Ut enim ad minim veniam</li><li>Incididunt ut labore et dolore magna</li><li>Esse cillum dolore eu fugiat nulla</li><li>Dolor in reprehenderit in voluptate</li><li>Nisi ut aliquip ex ea</li>
  </ul>
  <div class="foot"><div class="bar"></div><div class="url">www.keystoneharbor.com</div><div class="pg">13</div></div>
</section>

<!-- 8 team -->
<section class="slide">
  <div class="brand"><i></i><span>Keystone Harbor<br>Finance LLC.</span></div>
  <div class="hd" style="top:22px">Our Team</div>
  <div class="member" role="img" aria-label="Portrait photo of a team member" style="left:22px;top:64px"></div>
  <div class="member" role="img" aria-label="Portrait photo of a team member" style="left:115px;top:64px"></div>
  <div class="member" role="img" aria-label="Portrait photo of a team member" style="left:208px;top:64px"></div>
  <div class="name" style="left:22px;top:106px">Jonathan Doe</div>
  <div class="name" style="left:115px;top:106px">Jonathan Doe</div>
  <div class="name" style="left:208px;top:106px">Jonathan Doe</div>
  <p class="small" style="left:22px;top:116px;width:68px">Lorem ipsum dolor sit amet, consectetur adipiscing elit, sed do eiusmod tempor incididunt ut labore et dolore magna aliqua.</p>
  <p class="small" style="left:115px;top:116px;width:68px">Lorem ipsum dolor sit amet, consectetur adipiscing elit, sed do eiusmod tempor incididunt ut labore et dolore magna aliqua.</p>
  <p class="small" style="left:208px;top:116px;width:68px">Lorem ipsum dolor sit amet, consectetur adipiscing elit, sed do eiusmod tempor incididunt ut labore et dolore magna aliqua.</p>
  <p class="small" style="left:22px;top:150px;width:68px">Ut enim ad minim veniam, quis nostrud exercitation ullamco laboris nisi ut aliquip ex ea.</p>
  <p class="small" style="left:115px;top:150px;width:68px">Ut enim ad minim veniam, quis nostrud exercitation ullamco laboris nisi ut aliquip ex ea.</p>
  <p class="small" style="left:208px;top:150px;width:68px">Ut enim ad minim veniam, quis nostrud exercitation ullamco laboris nisi ut aliquip ex ea.</p>
  <div class="foot"><div class="bar"></div><div class="url">www.keystoneharbor.com</div><div class="pg">13</div></div>
</section>

<!-- 9 blue background -->
<section class="slide dark">
  <svg class="shapes" viewBox="0 0 237 178" preserveAspectRatio="none" role="img" aria-label="Faded photo of a city skyline">
    <defs><linearGradient id="sky" x1="0" y1="0" x2="1" y2="0"><stop offset="0" stop-color="#3a5990" stop-opacity="0"/><stop offset="1" stop-color="#5a74a2"/></linearGradient></defs>
    <polygon points="150,178 237,100 237,178" fill="url(#sky)"/>
  </svg>
  <div class="brand light"><i></i><span>Keystone Harbor<br>Finance LLC.</span></div>
  <div class="hd light" style="top:22px">Blue Background Slide</div>
  <svg class="abs" style="left:18px;top:76px;width:11px;height:11px" viewBox="0 0 12 12"><polygon points="6,0 12,3 0,3" fill="#fff"/><rect x="1" y="4" width="2" height="5" fill="#fff"/><rect x="5" y="4" width="2" height="5" fill="#fff"/><rect x="9" y="4" width="2" height="5" fill="#fff"/><rect x="0" y="10" width="12" height="2" fill="#fff"/></svg>
  <svg class="abs" style="left:160px;top:76px;width:11px;height:11px" viewBox="0 0 12 12"><rect x="0" y="7" width="2.5" height="5" fill="#fff"/><rect x="4" y="4" width="2.5" height="8" fill="#fff"/><rect x="8" y="1" width="2.5" height="11" fill="#fff"/></svg>
  <div class="abs" style="left:18px;top:96px;font:700 7.5px/1 'Merriweather',Georgia,serif;color:#fff">PLACE TITLE TEXT</div>
  <div class="abs" style="left:160px;top:96px;font:700 7.5px/1 'Merriweather',Georgia,serif;color:#fff">PLACE TITLE TEXT</div>
  <p class="small w" style="left:18px;top:108px;width:120px">Lorem ipsum dolor sit amet, consectetur adipiscing elit, sed do eiusmod tempor incididunt ut labore et dolore magna aliqua. Ut enim ad minim veniam, quis nostrud exercitation ullamco laboris nisi ut aliquip ex ea commodo consequat. Duis aute irure dolor in reprehenderit in voluptate velit esse cillum dolore eu fugiat nulla pariatur.</p>
  <p class="small w" style="left:160px;top:108px;width:120px">Lorem ipsum dolor sit amet, consectetur adipiscing elit, sed do eiusmod tempor incididunt ut labore et dolore magna aliqua. Ut enim ad minim veniam, quis nostrud exercitation ullamco laboris nisi ut aliquip ex ea commodo consequat. Duis aute irure dolor in reprehenderit in voluptate velit esse cillum dolore eu fugiat nulla pariatur.</p>
  <div class="foot"><div class="bar"></div><div class="url">www.keystoneharbor.com</div><div class="pg">13</div></div>
</section>

<!-- 10 graphs -->
<section class="slide">
  <div class="brand"><i></i><span>Keystone Harbor<br>Finance LLC.</span></div>
  <div class="hd" style="top:22px">Graphs and Charts</div>
  <svg class="abs" style="left:40px;top:50px;width:126px;height:70px" viewBox="0 0 126 70">
    <rect x="0" y="0" width="126" height="70" fill="#fff" stroke="#d5d8dd" stroke-width=".6"/>
    <g stroke="#e3e5e9" stroke-width=".5"><line x1="20" y1="6" x2="20" y2="60"/><line x1="45" y1="6" x2="45" y2="60"/><line x1="70" y1="6" x2="70" y2="60"/><line x1="95" y1="6" x2="95" y2="60"/><line x1="120" y1="6" x2="120" y2="60"/></g>
    <g fill="var(--navy)"><rect x="20" y="8" width="80" height="3"/><rect x="20" y="21" width="90" height="3"/><rect x="20" y="34" width="70" height="3"/><rect x="20" y="47" width="85" height="3"/></g>
    <g fill="#2b2f38"><rect x="20" y="12" width="95" height="3"/><rect x="20" y="25" width="75" height="3"/><rect x="20" y="38" width="88" height="3"/><rect x="20" y="51" width="62" height="3"/></g>
    <g font-family="Open Sans,sans-serif" font-size="3" fill="#666"><text x="6" y="13">2017</text><text x="6" y="26">2016</text><text x="6" y="39">2015</text><text x="6" y="52">2014</text><text x="18" y="66">0</text><text x="42" y="66">100</text><text x="67" y="66">200</text><text x="92" y="66">300</text><text x="114" y="66">400</text></g>
  </svg>
  <div class="abs" style="left:176px;top:56px;width:5px;height:5px;background:var(--navy)"></div>
  <div class="lbl" style="left:185px;top:56px;font-size:5px">Title Text</div>
  <p class="small" style="left:185px;top:63px;width:90px">Lorem ipsum dolor sit amet, consectetur adipiscing elit, sed do eiusmod.</p>
  <div class="abs" style="left:176px;top:86px;width:5px;height:5px;background:#2b2f38"></div>
  <div class="lbl" style="left:185px;top:86px;font-size:5px">Title Text</div>
  <p class="small" style="left:185px;top:93px;width:90px">Lorem ipsum dolor sit amet, consectetur adipiscing elit, sed do eiusmod.</p>
  <svg class="abs" style="left:16px;top:140px;width:46px;height:46px" viewBox="0 0 40 40">
    <circle cx="20" cy="20" r="20" fill="var(--navy)"/>
    <path d="M20 20 L20 0 A20 20 0 0 0 2 28 Z" fill="var(--grey)"/>
    <path d="M20 20 L2 28 A20 20 0 0 0 12 38 Z" fill="#2b2f38"/>
    <text x="25" y="24" font-family="Open Sans,sans-serif" font-size="4" fill="#fff">60%</text>
  </svg>
  <p class="body b" style="left:72px;top:146px;width:210px;font-size:5px">Lorem ipsum dolor sit amet, consectetur adipiscing elit, sed do eiusmod tempor incididunt ut labore et dolore magna aliqua. <span style="font-weight:400">Ut enim ad minim veniam, quis nostrud exercitation ullamco laboris nisi ut aliquip ex ea commodo consequat.</span></p>
  <div class="foot"><div class="bar"></div><div class="url">www.keystoneharbor.com</div><div class="pg">13</div></div>
</section>

<!-- 11 image and text -->
<section class="slide">
  <div class="brand"><i></i><span>Keystone Harbor<br>Finance LLC.</span></div>
  <div class="hd" style="top:22px">Image and Text Slide</div>
  <div class="photo" role="img" aria-label="Photo of an office tower with palm trees" style="left:0;top:54px;width:158px;height:132px;background:linear-gradient(180deg,#c9b59a,#7c6f5d 55%,#4f6a45)"></div>
  <div class="abs" style="left:158px;top:54px;width:140px;height:132px;background:var(--navy)"></div>
  <div class="abs" style="left:172px;top:80px;font:700 7.5px/1 'Merriweather',Georgia,serif;color:#fff">PLACE TITLE TEXT</div>
  <p class="small w" style="left:172px;top:92px;width:114px">Lorem ipsum dolor sit amet, consectetur adipiscing elit, sed do eiusmod tempor incididunt ut labore et dolore magna aliqua. Ut enim ad minim veniam, quis nostrud exercitation ullamco laboris nisi ut aliquip ex ea commodo consequat. Duis aute irure dolor in reprehenderit in voluptate velit esse cillum dolore eu fugiat nulla pariatur. Excepteur sint occaecat cupidatat non proident.</p>
  <div class="foot"><div class="bar"></div><div class="url">www.keystoneharbor.com</div><div class="pg">13</div></div>
</section>

<!-- 12 process -->
<section class="slide">
  <div class="brand"><i></i><span>Keystone Harbor<br>Finance LLC.</span></div>
  <div class="hd" style="top:22px">Our Process</div>
  <svg class="abs" style="left:112px;top:74px;width:76px;height:76px" viewBox="-40 -40 80 80">
    <g fill="var(--navy)">
      <path d="M2 -36 A36 36 0 0 1 36 -2 L17 -2 A17 17 0 0 0 2 -17 Z"/>
      <path d="M36 2 A36 36 0 0 1 2 36 L2 17 A17 17 0 0 0 17 2 Z"/>
      <path d="M-2 36 A36 36 0 0 1 -36 2 L-17 2 A17 17 0 0 0 -2 17 Z"/>
      <path d="M-36 -2 A36 36 0 0 1 -2 -36 L-2 -17 A17 17 0 0 0 -17 -2 Z"/>
    </g>
    <circle r="14" fill="var(--navy-soft)"/>
    <rect x="-5" y="-5" width="10" height="10" fill="#fff"/>
  </svg>
  <div class="lbl" style="left:14px;top:74px;font-size:6.5px">Text Title</div>
  <p class="body" style="left:14px;top:84px;width:92px">Lorem ipsum dolor sit amet, consectetur adipiscing elit, sed do eiusmod tempor incididunt ut labore et dolore</p>
  <div class="lbl" style="left:198px;top:74px;font-size:6.5px">Text Title</div>
  <p class="body" style="left:198px;top:84px;width:92px">Lorem ipsum dolor sit amet, consectetur adipiscing elit, sed do eiusmod tempor incididunt ut labore et dolore</p>
  <div class="lbl" style="left:14px;top:140px;font-size:6.5px">Text Title</div>
  <p class="body" style="left:14px;top:150px;width:92px">Lorem ipsum dolor sit amet, consectetur adipiscing elit, sed do eiusmod tempor incididunt ut labore et dolore</p>
  <div class="lbl" style="left:198px;top:140px;font-size:6.5px">Text Title</div>
  <p class="body" style="left:198px;top:150px;width:92px">Lorem ipsum dolor sit amet, consectetur adipiscing elit, sed do eiusmod tempor incididunt ut labore et dolore</p>
  <div class="foot"><div class="bar"></div><div class="url">www.keystoneharbor.com</div><div class="pg">13</div></div>
</section>

<!-- 13 chart -->
<section class="slide">
  <div class="brand"><i></i><span>Keystone Harbor<br>Finance LLC.</span></div>
  <div class="hd" style="top:22px">Chart Slide</div>
  <svg class="abs" style="left:14px;top:46px;width:120px;height:150px" viewBox="0 0 120 150">
    <rect x="0" y="0" width="120" height="150" fill="#fff" stroke="#d5d8dd" stroke-width=".6"/>
    <g stroke="#e3e5e9" stroke-width=".5"><line x1="8" y1="30" x2="114" y2="30"/><line x1="8" y1="60" x2="114" y2="60"/><line x1="8" y1="90" x2="114" y2="90"/><line x1="8" y1="120" x2="114" y2="120"/></g>
    <g fill="var(--navy)"><rect x="14" y="62" width="5" height="58"/><rect x="40" y="38" width="5" height="82"/><rect x="66" y="50" width="5" height="70"/><rect x="92" y="30" width="5" height="90"/></g>
    <g fill="#2b2f38"><rect x="20" y="88" width="5" height="32"/><rect x="46" y="80" width="5" height="40"/><rect x="72" y="72" width="5" height="48"/><rect x="98" y="42" width="5" height="78"/></g>
    <g fill="var(--grey)"><rect x="26" y="96" width="5" height="24"/><rect x="52" y="92" width="5" height="28"/><rect x="78" y="86" width="5" height="34"/><rect x="104" y="22" width="5" height="98"/></g>
    <g font-family="Open Sans,sans-serif" font-size="3.2" fill="#555"><text x="12" y="127">Category 1</text><text x="38" y="127">Category 2</text><text x="64" y="127">Category 3</text><text x="90" y="127">Category 4</text></g>
    <g font-family="Open Sans,sans-serif" font-size="3.6" fill="var(--navy)" font-weight="700"><rect x="10" y="136" width="4" height="4" fill="var(--navy)"/><text x="16" y="139.5">Title Text</text><rect x="46" y="136" width="4" height="4" fill="#2b2f38"/><text x="52" y="139.5">Title Text</text><rect x="82" y="136" width="4" height="4" fill="var(--grey)"/><text x="88" y="139.5">Title Text</text></g>
  </svg>
  <div class="sub" style="left:162px;top:50px">Subtitle Goes Here</div>
  <p class="small" style="left:162px;top:60px;width:120px">Lorem ipsum dolor sit amet, consectetur adipiscing elit, sed do eiusmod tempor incididunt ut labore et dolore magna aliqua. Ut enim ad minim veniam, quis nostrud exercitation ullamco laboris nisi ut aliquip ex ea commodo consequat. Duis aute irure dolor in reprehenderit in voluptate velit esse cillum dolore eu fugiat nulla pariatur. Excepteur sint occaecat cupidatat non proident, sunt in culpa qui officia deserunt mollit anim id est laborum. Sed ut perspiciatis unde omnis iste natus error sit voluptatem accusantium doloremque laudantium, totam rem aperiam, eaque ipsa quae ab illo inventore veritatis et quasi architecto beatae vitae dicta sunt explicabo.</p>
  <div class="foot"><div class="bar"></div><div class="url">www.keystoneharbor.com</div><div class="pg">13</div></div>
</section>

<!-- 14 why us -->
<section class="slide">
  <svg class="shapes" viewBox="0 0 298 223" preserveAspectRatio="none">
    <defs><linearGradient id="hands" x1="0" y1="0" x2="1" y2="1"><stop offset="0" stop-color="#a7b3c6"/><stop offset="1" stop-color="#4d6591"/></linearGradient></defs>
    <polygon points="205,0 298,0 298,223 108,223" fill="url(#hands)" role="img" aria-label="Blue-tinted photo of a business handshake"/>
    <polygon points="290,0 298,0 298,223 190,223" fill="var(--navy)" opacity=".35"/>
  </svg>
  <div class="brand light"><i></i><span>Keystone Harbor<br>Finance LLC.</span></div>
  <div class="hd" style="top:22px">Why Us</div>
  <p class="body" style="left:12px;top:52px;width:132px;font-size:5.8px">Lorem ipsum dolor sit amet, consectetur adipiscing elit, sed do eiusmod tempor incididunt ut labore et dolore magna aliqua. Ut enim ad minim veniam, quis nostrud exercitation ullamco laboris nisi ut aliquip ex ea commodo consequat. Duis aute irure dolor in reprehenderit in voluptate velit esse cillum dolore eu fugiat nulla pariatur.</p>
  <div class="foot"><div class="bar"></div><div class="url">www.keystoneharbor.com</div><div class="pg">13</div></div>
</section>

<!-- 15 contact -->
<section class="slide">
  <div class="abs" style="left:40px;top:42px;display:flex;align-items:center;gap:7px;font:700 13px/1.15 'Merriweather',Georgia,serif;color:var(--navy);text-transform:uppercase">
    <i style="display:block;width:24px;height:24px;background:var(--navy)"></i><span>Keystone Harbor<br>Finance LLC.</span>
  </div>
  <div class="abs" style="left:40px;top:140px;font:700 9px/1 'Open Sans',Arial,sans-serif;color:var(--navy)">Contact Us</div>
  <ul class="contact">
    <li><svg viewBox="0 0 10 10"><circle cx="5" cy="5" r="5" fill="var(--navy)"/><path d="M3 2.5 L4.2 2.5 L4.6 4 L3.9 4.6 Q4.6 5.8 5.6 6.2 L6.1 5.5 L7.5 6 L7.5 7.2 Q4 7.5 2.8 3.2 Z" fill="#fff"/></svg>(555) 014-2290</li>
    <li><svg viewBox="0 0 10 10"><circle cx="5" cy="5" r="5" fill="var(--navy)"/><rect x="2.5" y="3.3" width="5" height="3.5" fill="none" stroke="#fff" stroke-width=".7"/><path d="M2.5 3.3 L5 5.2 L7.5 3.3" fill="none" stroke="#fff" stroke-width=".7"/></svg>hello@keystoneharbor.com</li>
    <li><svg viewBox="0 0 10 10"><circle cx="5" cy="5" r="5" fill="var(--navy)"/><circle cx="5" cy="5" r="2.6" fill="none" stroke="#fff" stroke-width=".6"/><line x1="2.4" y1="5" x2="7.6" y2="5" stroke="#fff" stroke-width=".6"/><ellipse cx="5" cy="5" rx="1.1" ry="2.6" fill="none" stroke="#fff" stroke-width=".6"/></svg>www.keystoneharbor.com</li>
    <li><svg viewBox="0 0 10 10"><circle cx="5" cy="5" r="5" fill="var(--navy)"/><path d="M5 8 L3 5 A2.2 2.2 0 1 1 7 5 Z" fill="#fff"/><circle cx="5" cy="4.3" r=".8" fill="var(--navy)"/></svg>Street No., Location</li>
  </ul>
  <svg class="shapes" viewBox="0 0 298 223" preserveAspectRatio="none">
    <defs><linearGradient id="map" x1="0" y1="0" x2="1" y2="1"><stop offset="0" stop-color="#e6e9ee"/><stop offset="1" stop-color="#c9d4e0"/></linearGradient></defs>
    <polygon points="180,140 240,108 298,130 298,160 240,190" fill="var(--navy)"/>
    <polygon points="222,196 262,172 298,190 298,223 240,223" fill="url(#map)" role="img" aria-label="Street map showing the office location"/>
  </svg>
</section>

</main>
</body>
</html>
```